Web Site Design for a Finance (lending) Company

We are opening a new subsidiary that focuses on lending money in the real estate industry. We need a web site designed to represent the business.

The business is lending money to real estate investors. A typical client/borrower will be looking to borrow money to buy a house, renovate it and then sell it at a profit, all within 12 months or less.

Company name is RTV Finance. Our logo is attached.

Attached is a general outline for the web site. We're working on writing more text for each page but this should give you enough to get started with some ideas.

Competitor web site that I like a lot (as an example): https://dorvaleqcapital.example/. Many of the general items on this site match what we will need (description of loan programs, FAQ)

Target Market(s)

Real estate investors (generally individuals or small companies with just a few people) who are buying homes, renovating them and then selling them at a profit.

Industry/Entity Type

Finance

Coding

Coded - Design and coding required

Number of Pages Required

5+ page

Colors

Designer to choose colors to be used in the design.

Requirements
Must have
• Minimalist design. Clean lines without too much clutter. Some stock photography is ok but the photos should not be distracting. They should almost fade in to the background so that user can focus on the key information about what our company does instead. We are a finance company, not a design company, so the information about our products will be more interesting to site visitors than the art.
• Some minimalist examples from Snapboard:
• https://www.snapboardia.example/explore/minimalist-web-design/
Nice to have
• If you search in zoovle for "hard money lenders" you will find many examples of web sites from our competition. I have provided a link above to competitor web site that I like a lot.
• I have attached our logo in EPS format. Logo is green. Web site doesn't have to be green but it should be of a color that will work well with the logo.

```html
<!DOCTYPE html>
<html lang="en">
<head>
<meta charset="utf-8">
<title>RTV Finance</title>
<link rel="stylesheet" href="https://fonts.googleapis.com/css2?family=Maven+Pro:wght@400;500;600&family=Roboto:ital,wght@0,400;1,400&family=Arimo:ital,wght@0,400;0,700;1,400&display=swap">
<style>
:root{
  --green:#0c5236;
  --green-dark:#094329;
  --ink:#2f3336;
  --muted:#6b6f73;
  --slate:#8e9296;
  --slate-dark:#7d8185;
  --footer:#3b3d40;
  --white:#ffffff;
  --head:"Maven Pro",sans-serif;
  --body:"Arimo",sans-serif;
}
*{box-sizing:border-box;margin:0;padding:0}
html,body{width:1200px;height:4265px;overflow:hidden;background:var(--white)}
body{font-family:var(--body);color:var(--ink);position:relative}
section,header,footer{position:relative;width:1200px;overflow:hidden}
.abs{position:absolute}
.photo{position:absolute}

/* header */
.site-header{height:114px;background:var(--white)}
.brand{left:85px;top:36px;font-family:var(--head);font-weight:600;font-size:30px;color:var(--green);display:flex;align-items:center;gap:12px}
.brand-dot{width:22px;height:22px;background:var(--green)}
.main-nav{right:80px;top:46px;display:flex;gap:44px;font-family:var(--head);font-size:18px;color:#8b8f93;align-items:center}
.main-nav .active{color:var(--green)}

/* hero */
.hero{height:569px}
.hero .photo{inset:0;background:linear-gradient(180deg,#6d8fb4 0%,#a7b3a9 30%,#8f8069 55%,#5d6b45 78%,#3f5a30 100%)}
.hero .shade{position:absolute;inset:0;background:rgba(20,25,22,.25)}
.hero h1{position:absolute;top:128px;width:100%;text-align:center;font-family:"Roboto",sans-serif;font-weight:400;font-size:50px;line-height:58px;color:var(--white)}
.hero .tagline{position:absolute;top:250px;width:100%;text-align:center;font-family:"Roboto",sans-serif;font-style:italic;font-size:25px;color:var(--white)}
.btn{position:absolute;display:flex;align-items:center;justify-content:center;border-radius:30px;font-family:var(--head);font-size:19px;text-transform:uppercase}
.btn-green{background:var(--green);color:var(--white)}
.btn-white{background:var(--white);color:var(--green)}
.hero .btn{left:498px;top:298px;width:204px;height:52px}

/* headings */
.section-title{position:absolute;width:100%;text-align:center;font-family:var(--head);font-weight:400;font-size:40px;color:var(--muted)}
.section-title b{font-weight:500;color:var(--green)}
.title-rule{position:absolute;left:430px;width:340px;height:14px}

/* about */
.about{height:781px}
.circle{position:absolute;border-radius:50%;border:2px dashed #9aa0a5}
.circle .photo{inset:8px;border-radius:50%}
.about p{position:absolute;left:185px;width:830px;top:566px;text-align:center;font-size:15px;line-height:27px;color:var(--muted)}
.about .btn{left:485px;top:664px;width:230px;height:52px}

/* loan rows */
.loan{height:412px}
.loan h2{position:absolute;font-family:var(--head);font-weight:400;font-size:28px;color:var(--white)}
.loan p{position:absolute;width:470px;font-size:15px;line-height:26px;color:var(--white)}
.loan .btn{width:176px;height:50px}
.flip .photo{left:0;top:0;width:640px;height:412px;background:linear-gradient(180deg,#c9d2d6 0%,#a79a86 45%,#7a5a45 65%,#4f6b37 100%)}
.flip .panel{position:absolute;left:590px;top:0;width:610px;height:412px;background:var(--green);clip-path:polygon(8% 0,100% 0,100% 100%,0 100%)}
.commercial{height:413px}
.commercial .photo{left:560px;top:0;width:640px;height:413px;background:linear-gradient(180deg,#7fa3c8 0%,#b7c3cc 40%,#8e9aa1 65%,#9c9a94 100%)}
.commercial .panel{position:absolute;left:0;top:0;width:650px;height:413px;background:var(--green);clip-path:polygon(0 0,88% 0,100% 100%,0 100%)}

/* testimonial */
.testimonial{height:483px;overflow:visible}
.quote-badge{position:absolute;left:560px;top:-40px;width:80px;height:80px;border-radius:50%;background:var(--slate-dark);color:var(--white);font-family:Georgia,serif;font-size:70px;line-height:112px;text-align:center;z-index:2}
.avatar{position:absolute;border-radius:50%;background:linear-gradient(180deg,#dfe3e6,#aeb6bd);border:4px solid var(--white);box-shadow:0 0 0 1px #c4c8cc}
.testimonial p{position:absolute;left:185px;width:830px;top:308px;text-align:center;font-size:15px;line-height:26px;color:var(--muted)}
.testimonial .name{position:absolute;top:402px;width:100%;text-align:center;font-size:16px;color:var(--ink)}

/* contact */
.contact{height:333px;background:var(--slate)}
.contact .photo{left:200px;top:0;width:440px;height:333px;background:linear-gradient(180deg,#9a9ea2 0%,#6f7377 100%)}
.contact h2{position:absolute;left:674px;top:28px;font-family:var(--head);font-weight:400;font-size:36px;color:var(--white)}
.field{position:absolute;border:1.5px solid var(--white);color:var(--white);font-size:14px;padding:8px 10px}
.submit{position:absolute;left:904px;top:253px;width:216px;height:37px;background:#b9bbbe;color:var(--white);font-family:var(--head);font-size:20px;display:flex;align-items:center;justify-content:center}

/* blog */
.blog{height:526px}
.blog .section-title{top:56px;color:var(--green);font-size:38px}
.card{position:absolute;top:131px;width:332px}
.card .photo{position:relative;height:162px}
.card .avatar{left:30px;top:130px;width:62px;height:62px;border-width:3px}
.card .date{position:absolute;left:112px;top:168px;font-size:12px;font-style:italic;color:var(--muted)}
.card h3{position:absolute;top:208px;font-family:var(--body);font-weight:400;font-size:18px;color:var(--green);white-space:nowrap}
.card p{position:absolute;top:236px;width:300px;font-size:13px;line-height:20px;color:var(--muted)}
.card .more{position:absolute;top:282px;font-size:14px;color:var(--ink);text-decoration:underline}

/* subscribe */
.subscribe{height:165px;background:var(--slate-dark)}
.subscribe h2{position:absolute;left:80px;top:40px;font-family:var(--head);font-weight:400;font-size:24px;color:var(--white)}
.subscribe p{position:absolute;left:80px;top:80px;width:540px;font-size:15px;line-height:24px;color:var(--white)}
.signup{position:absolute;left:705px;top:57px;width:418px;height:60px;border-radius:30px;background:var(--white)}
.signup span{position:absolute;left:55px;top:21px;font-size:14px;color:var(--muted)}
.signup .btn{left:258px;top:6px;width:154px;height:48px;font-size:19px}

/* footer */
.site-footer{height:407px;background:var(--footer)}
.foot-brand{position:absolute;width:100%;top:62px;text-align:center;font-family:var(--head);font-weight:600;font-size:38px;color:var(--white)}
.foot-nav{position:absolute;left:80px;top:176px;display:flex;align-items:center;gap:30px;font-size:14px;color:var(--white)}
.foot-nav .pill{background:var(--green);border-radius:26px;padding:13px 24px}
.foot-nav .sep{color:#9a9ea2}
.social{position:absolute;top:173px;width:52px;height:52px;border-radius:50%;background:var(--green)}
.foot-rule{position:absolute;left:80px;top:241px;width:1040px;height:1px;background:#77797c}
.site-footer h2{position:absolute;left:65px;top:264px;font-family:var(--head);font-weight:400;font-size:23px;color:var(--white)}
.info{position:absolute;top:308px;display:flex;align-items:center;gap:20px;font-size:13px;line-height:18px;color:var(--white)}
.info .icon{width:50px;height:50px;border-radius:50%;background:var(--green);display:flex;align-items:center;justify-content:center;flex:none}
.legal{height:61px;background:var(--green-dark);color:var(--white);font-size:14px;display:flex;align-items:center;justify-content:center}
</style>
</head>
<body>

<header class="site-header">
  <div class="brand abs"><span class="brand-dot"></span>RTV Finance</div>
  <nav class="main-nav abs">
    <span class="active">Home</span><span>About Us</span><span>Loans</span><span>Resources</span><span>Contact Us</span>
    <svg width="24" height="24" viewBox="0 0 24 24" fill="none" stroke="#0c5236" stroke-width="2"><circle cx="10" cy="10" r="7"/><path d="M15 15l6 6"/></svg>
  </nav>
</header>

<section class="hero">
  <div class="photo" role="img" aria-label="Photo of a two-storey suburban house with palm trees"></div>
  <div class="shade"></div>
  <h1>Local real estate experts lending to<br>local real estate investors</h1>
  <div class="tagline">focuses on lending money in the real estate industry</div>
  <a class="btn btn-green">Read More</a>
</section>

<section class="about">
  <h2 class="section-title" style="top:45px">About <b>RTV</b> Finance</h2>
  <svg class="title-rule" style="top:104px" viewBox="0 0 340 14"><path d="M0 3H160L170 11L180 3H340" fill="none" stroke="#0c5236" stroke-width="2"/></svg>
  <div class="circle" style="left:318px;top:150px;width:246px;height:246px"><div class="photo" role="img" aria-label="Photo of a family home" style="background:linear-gradient(180deg,#b8c0c6,#6e6a64 60%,#4d5a3e)"></div></div>
  <div class="circle" style="left:631px;top:150px;width:246px;height:246px"><div class="photo" role="img" aria-label="Photo of a modern office building" style="background:linear-gradient(180deg,#8fb1d4,#5f6f7c 60%,#8a8b88)"></div></div>
  <div class="circle" style="left:473px;top:292px;width:254px;height:254px;border:7px solid var(--green)"><div class="photo" role="img" aria-label="Photo of a home interior tinted green" style="inset:0;background:linear-gradient(180deg,#3f7a5c,#1e5a3c)"></div></div>
  <p>Lorem Ipsum is simply dummy text of the printing and typesetting industry. Lorem Ipsum has been the industry's standard dummy text ever since the 1500s, when an unknown printer took a galley of type and scrambled it to make a type specimen book.</p>
  <a class="btn btn-green">Read About Us</a>
</section>

<section class="loan flip">
  <div class="photo" role="img" aria-label="Photo of a brick family house with a lawn"></div>
  <div class="panel"></div>
  <h2 style="left:665px;top:50px">RTV Fix and Flip Loans</h2>
  <svg class="abs" style="left:665px;top:98px" width="250" height="14" viewBox="0 0 250 14"><path d="M0 7H110M140 7H250" stroke="#fff" stroke-width="1.5"/><path d="M118 11L132 3" stroke="#fff" stroke-width="2"/></svg>
  <p style="left:665px;top:130px">Lorem Ipsum is simply dummy text of the printing and typesetting industry. Lorem Ipsum has been the industry's standard dummy text ever since the 1500s, when an unknown printer took a galley of type and scrambled it to make a type specimen book. It has survived not only five centuries, but also the leap into electronic typesetting, remaining essentially unchanged.</p>
  <a class="btn btn-white" style="left:665px;top:316px">Read More</a>
</section>

<section class="loan commercial">
  <div class="photo" role="img" aria-label="Photo of a glass commercial office complex"></div>
  <div class="panel"></div>
  <h2 style="left:80px;top:52px">RTV Commercial Hard Money Loans</h2>
  <svg class="abs" style="left:80px;top:100px" width="470" height="14" viewBox="0 0 470 14"><path d="M0 7H220M250 7H470" stroke="#fff" stroke-width="1.5"/><path d="M228 11L242 3" stroke="#fff" stroke-width="2"/></svg>
  <p style="left:80px;top:132px">Lorem Ipsum is simply dummy text of the printing and typesetting industry. Lorem Ipsum has been the industry's standard dummy text ever since the 1500s, when an unknown printer took a galley of type and scrambled it to make a type specimen book. It has survived not only five centuries, but also the leap into electronic typesetting, remaining essentially unchanged.</p>
  <a class="btn btn-white" style="left:80px;top:316px">Read More</a>
</section>

<section class="testimonial">
  <div class="quote-badge">&#8220;</div>
  <h2 class="section-title" style="top:58px;font-size:38px">What <b>Our Client Say</b></h2>
  <div class="avatar" role="img" aria-label="Portrait of the client" style="left:532px;top:138px;width:136px;height:136px"></div>
  <p>Lorem Ipsum is simply dummy text of the printing and typesetting industry. Lorem Ipsum has been the industry's standard dummy text ever since the 1500s, when an unknown printer took a galley of type and scrambled it to make a type specimen book. It has survived not only five centuries.</p>
  <div class="name">- ABC KATTY</div>
</section>

<section class="contact">
  <div class="photo" role="img" aria-label="Photo of a businesswoman holding a red folder"></div>
  <h2>Contact Form</h2>
  <div class="field" style="left:674px;top:92px;width:213px;height:36px">First Name* :</div>
  <div class="field" style="left:904px;top:92px;width:216px;height:36px">Last Name* :</div>
  <div class="field" style="left:674px;top:137px;width:213px;height:36px">Loan type :</div>
  <div class="field" style="left:904px;top:137px;width:216px;height:36px">E-Mail* :</div>
  <div class="field" style="left:674px;top:180px;width:446px;height:63px">Company Name* :</div>
  <div class="field" style="left:674px;top:253px;width:213px;height:37px">Phone No* :</div>
  <div class="submit">SUBMIT</div>
</section>

<section class="blog">
  <h2 class="section-title">Latest New Blog</h2>
  <article class="card" style="left:80px">
    <div class="photo" role="img" aria-label="Photo of a stone family house" style="background:linear-gradient(180deg,#9cc0e0,#6b5a4c 60%,#5d7a3b)"></div>
    <div class="avatar" role="img" aria-label="Author portrait"></div>
    <div class="date">Posted October 03, 2017</div>
    <h3>Lorem Ipsum is simply dummy text of</h3>
    <p>Lorem Ipsum is simply dummy text of the printing and typesetting text of the industry.</p>
    <div class="more">READ MORE</div>
  </article>
  <article class="card" style="left:435px">
    <div class="photo" role="img" aria-label="Photo of a bright living room interior" style="background:linear-gradient(180deg,#d8d6d2,#b7b3ac 60%,#8d8780)"></div>
    <div class="avatar" role="img" aria-label="Author portrait"></div>
    <div class="date">Posted October 03, 2017</div>
    <h3>Lorem Ipsum is simply dummy text of</h3>
    <p>Lorem Ipsum is simply dummy text of the printing and typesetting text of the industry.</p>
    <div class="more">READ MORE</div>
  </article>
  <article class="card" style="left:788px">
    <div class="photo" role="img" aria-label="Photo of a red wooden house among trees" style="background:linear-gradient(180deg,#8fb8de,#a8442e 55%,#4f7a36)"></div>
    <div class="avatar" role="img" aria-label="Author portrait"></div>
    <div class="date">Posted October 03, 2017</div>
    <h3>Lorem Ipsum is simply dummy text of</h3>
    <p>Lorem Ipsum is simply dummy text of the printing and typesetting text of the industry.</p>
    <div class="more">READ MORE</div>
  </article>
</section>

<section class="subscribe">
  <h2>STAY TUNED WITH US</h2>
  <p>Subscribe now and receive weekly newsletter with educational materials, new courses, interesting posts, popular books and much more!</p>
  <div class="signup">
    <svg class="abs" style="left:24px;top:22px" width="20" height="16" viewBox="0 0 20 16" fill="none" stroke="#555" stroke-width="1.5"><rect x="1" y="1" width="18" height="14"/><path d="M1 1l9 7 9-7"/></svg>
    <span>Enter Email id :</span>
    <a class="btn btn-green">Subscribe</a>
  </div>
</section>

<footer class="site-footer">
  <div class="foot-brand">RTV Finance</div>
  <nav class="foot-nav">
    <span class="pill">Home</span><span class="sep">|</span><span>About Us</span><span class="sep">|</span><span>Loans</span><span class="sep">|</span><span>Resources</span><span class="sep">|</span><span>Contact</span>
  </nav>
  <span class="social" style="left:941px"></span>
  <span class="social" style="left:1009px"></span>
  <span class="social" style="left:1072px"></span>
  <div class="foot-rule"></div>
  <h2>CONTACT US</h2>
  <div class="info" style="left:80px">
    <span class="icon"><svg width="18" height="22" viewBox="0 0 18 22" fill="#fff"><path d="M9 0a8 8 0 0 0-8 8c0 6 8 14 8 14s8-8 8-14a8 8 0 0 0-8-8zm0 11a3 3 0 1 1 0-6 3 3 0 0 1 0 6z"/></svg></span>
    <span>101- Lorem Ipsum is simple<br>dummy text of print</span>
  </div>
  <div class="info" style="left:345px">
    <span class="icon"><svg width="20" height="20" viewBox="0 0 24 24" fill="#fff"><path d="M6.6 10.8a15 15 0 0 0 6.6 6.6l2.2-2.2a1 1 0 0 1 1-.25 11.4 11.4 0 0 0 3.6.6 1 1 0 0 1 1 1V20a1 1 0 0 1-1 1A17 17 0 0 1 3 4a1 1 0 0 1 1-1h3.5a1 1 0 0 1 1 1c0 1.25.2 2.45.6 3.6a1 1 0 0 1-.25 1z"/></svg></span>
    <span>123 456 7890</span>
  </div>
  <div class="info" style="left:615px">
    <span class="icon"><svg width="20" height="20" viewBox="0 0 20 20" fill="#fff"><rect x="5" y="1" width="10" height="5"/><rect x="1" y="7" width="18" height="8" rx="1"/><rect x="5" y="12" width="10" height="7" fill="#0c5236" stroke="#fff" stroke-width="1.5"/></svg></span>
    <span>123 456 7890</span>
  </div>
  <div class="info" style="left:871px">
    <span class="icon"><svg width="20" height="16" viewBox="0 0 20 16" fill="#fff"><path d="M0 2l10 7 10-7V0H0zM0 4v12h20V4l-10 7z"/></svg></span>
    <span>info@rtvlending.example</span>
  </div>
</footer>

<div class="legal">© RTV Finance - 2017. All Rights Reserved.</div>

</body>
</html>
```